dobbo's business card for earthmoving and tipper hire business.

I have a small earthmoving and tipper truck company. I am aiming for the smaller jobs that the big guys don't want. I am also Doing grass slashing and fire hazard reduction work. I would like to see some earthy colors, greens browns etc. I have a tractor with a front end loader attachment, and a 22 ton tipper. I would like to maybe have a silhouette of a tipper and tractor/slasher/loader setup in centre with my business name over the top and details to one side or something like that

Industry/Entity Type

Business

Contact Information for Business Card

Dobbo's small earthworks and tipper hireToowoombaABN: 47781050480PH 0479126773Email dobbo.3@farrowpost.com

Font styles to use
Sans Serif

Colors
fbee3d
abd036
85cae6
f78f20

Requirements
Nice to have
• Earthy colors . business name in blue

```html
<!DOCTYPE html>
<html lang="en">
<head>
<meta charset="utf-8">
<title>Dobbo's Small Earthworks and Tipper Hire — Business Card</title>
<link rel="stylesheet" href="https://fonts.googleapis.com/css2?family=Saira:wght@400;700&display=swap">
<style>
  :root {
    --page-bg: #ececec;
    --ink-dark: #2d2a26;
    --white: #ffffff;
    --forest: #0d4d22;
    --forest-title: #b7d452;
    --forest-swoosh: #f08a1c;
    --forest-field: #c8d850;
    --forest-bullet: #b7d452;
    --earth: #52270f;
    --earth-title: #fff200;
    --earth-swoosh: #fff200;
    --earth-field: #abcb1f;
    --earth-bullet: #fff200;
  }
  * { box-sizing: border-box; margin: 0; padding: 0; }
  html, body { width: 1020px; height: 1200px; overflow: hidden; }
  body { background: var(--page-bg); position: relative; }

  .card {
    position: absolute;
    width: 810px; height: 470px;
    overflow: hidden;
    background: var(--field);
  }
  .card--forest { left: 97px; top: 66px;
    --band: var(--forest); --title: var(--forest-title); --swoosh: var(--forest-swoosh);
    --field: var(--forest-field); --bullet: var(--forest-bullet); }
  .card--earth { left: 99px; top: 607px;
    --band: var(--earth); --title: var(--earth-title); --swoosh: var(--earth-swoosh);
    --field: var(--earth-field); --bullet: var(--earth-bullet); }

  .card__backdrop { position: absolute; inset: 0; width: 810px; height: 470px; }
  .card__backdrop .band { fill: var(--band); }
  .card__backdrop .swoosh { fill: var(--swoosh); }

  .card__title {
    position: absolute; left: 0; right: 0; top: 40px;
    text-align: center;
    white-space: nowrap;
    font-family: "Saira", sans-serif;
    font-weight: 700; font-size: 27px; letter-spacing: 0.2px;
    line-height: 36px;
    text-transform: uppercase;
    color: var(--title);
  }

  .machine {
    position: absolute;
    border-radius: 10px;
    background: linear-gradient(160deg, rgba(255,255,255,0.95), rgba(255,255,255,0.78));
  }
  .machine--loader { left: 40px; top: 86px; width: 217px; height: 113px; }
  .machine--tipper { left: 255px; top: 120px; width: 174px; height: 163px; }

  .services {
    position: absolute; left: 452px; top: 126px;
    list-style: none;
    font-family: "Saira", sans-serif;
    font-weight: 700; font-size: 23px; line-height: 33px;
    white-space: nowrap;
    color: var(--white);
  }
  .services li::before {
    content: "";
    display: inline-block;
    width: 8px; height: 8px; border-radius: 50%;
    background: var(--bullet);
    margin-right: 8px; vertical-align: middle; position: relative; top: -2px;
  }

  .contact {
    position: absolute; left: 48px; top: 326px;
    list-style: none;
    font-family: "Saira", sans-serif;
    font-weight: 400; font-size: 23px; line-height: 34px;
    color: var(--ink-dark);
  }
  .contact li { display: flex; align-items: center; }
  .contact svg { width: 24px; height: 24px; margin-right: 10px; flex: none; }
  .contact svg * { fill: none; stroke: var(--ink-dark); stroke-width: 1.8; }
  .contact svg .solid { fill: var(--ink-dark); stroke: none; }

  .abn {
    position: absolute; left: 453px; top: 394px;
    font-family: "Saira", sans-serif;
    font-size: 23px; line-height: 34px;
    color: var(--ink-dark);
  }
</style>
</head>
<body>

<section class="card card--forest">
  <svg class="card__backdrop" viewBox="0 0 810 470" aria-hidden="true">
    <path class="band" d="M0 0 H810 V300 C700 332 600 346 515 344 C330 340 120 262 0 150 Z"/>
    <path class="swoosh" d="M0 132 C120 244 330 326 515 332 C600 334 700 322 810 292 V298 C700 328 600 340 515 338 C330 334 120 254 0 146 Z"/>
  </svg>
  <h1 class="card__title">Dobbo's Small Earthworks and Tipper Hire</h1>
  <div class="machine machine--loader" role="img" aria-label="White silhouette of a tractor with front end loader and slasher"></div>
  <div class="machine machine--tipper" role="img" aria-label="White silhouette of a tipper truck with raised tray"></div>
  <ul class="services">
    <li>Small earthworks</li>
    <li>Slashing</li>
    <li>Fire hazard reduction</li>
    <li>Rural cleanups</li>
    <li>Tipper</li>
  </ul>
  <ul class="contact">
    <li><svg viewBox="0 0 24 24" aria-hidden="true"><path class="solid" d="M7 2 L10 2 L11 7 L8.5 8.5 C9.5 12 11 15 13.5 17 L16 15.5 L19 19 L17 22 C9 21 4 11 6 3 Z"/></svg>0412583906</li>
    <li><svg viewBox="0 0 24 24" aria-hidden="true"><rect x="3" y="6" width="18" height="12"/><path d="M3 6 L12 13 L21 6 M3 18 L10 11.5 M21 18 L14 11.5"/></svg>dobbo.3@farrowpost.com</li>
    <li><svg viewBox="0 0 24 24" aria-hidden="true"><path class="solid" d="M12 1 C7.5 1 5 4.5 5 8 C5 13 12 23 12 23 C12 23 19 13 19 8 C19 4.5 16.5 1 12 1 Z M12 5 A3 3 0 1 0 12.01 5 Z" fill-rule="evenodd"/></svg>Ridgevale</li>
  </ul>
  <p class="abn">ABN: 51603928174</p>
</section>

<section class="card card--earth">
  <svg class="card__backdrop" viewBox="0 0 810 470" aria-hidden="true">
    <path class="band" d="M0 0 H810 V300 C700 332 600 346 515 344 C330 340 120 262 0 150 Z"/>
    <path class="swoosh" d="M0 132 C120 244 330 326 515 332 C600 334 700 322 810 292 V298 C700 328 600 340 515 338 C330 334 120 254 0 146 Z"/>
  </svg>
  <h1 class="card__title">Dobbo's Small Earthworks and Tipper Hire</h1>
  <div class="machine machine--loader" role="img" aria-label="White silhouette of a tractor with front end loader and slasher"></div>
  <div class="machine machine--tipper" role="img" aria-label="White silhouette of a tipper truck with raised tray"></div>
  <ul class="services">
    <li>Small earthworks</li>
    <li>Slashing</li>
    <li>Fire hazard reduction</li>
    <li>Rural cleanups</li>
    <li>Tipper</li>
  </ul>
  <ul class="contact">
    <li><svg viewBox="0 0 24 24" aria-hidden="true"><path class="solid" d="M7 2 L10 2 L11 7 L8.5 8.5 C9.5 12 11 15 13.5 17 L16 15.5 L19 19 L17 22 C9 21 4 11 6 3 Z"/></svg>0412583906</li>
    <li><svg viewBox="0 0 24 24" aria-hidden="true"><rect x="3" y="6" width="18" height="12"/><path d="M3 6 L12 13 L21 6 M3 18 L10 11.5 M21 18 L14 11.5"/></svg>dobbo.3@farrowpost.com</li>
    <li><svg viewBox="0 0 24 24" aria-hidden="true"><path class="solid" d="M12 1 C7.5 1 5 4.5 5 8 C5 13 12 23 12 23 C12 23 19 13 19 8 C19 4.5 16.5 1 12 1 Z M12 5 A3 3 0 1 0 12.01 5 Z" fill-rule="evenodd"/></svg>Ridgevale</li>
  </ul>
  <p class="abn">ABN: 51603928174</p>
</section>

</body>
</html>
```